Construction business card

I need a new business card, they can connect with my logo, brand.
What we do is residential house , design and build
I like: Navy blue / black
I attached our logo, brand,
and, some idea for business card.

```html
<!DOCTYPE html>
<html lang="en">
<head>
<meta charset="utf-8">
<title>Harlow Ridge Builders – Business Card</title>
<link href="https://fonts.googleapis.com/css2?family=Arimo:wght@400;700&display=swap" rel="stylesheet">
<style>
  :root {
    --stage: #1b1b1b;
    --card: #262626;
    --card-back: #232323;
    --brand-blue: #3a8bd0;
    --ink-light: #ffffff;
    --ink-soft: #e6e6e6;
    --emboss: #3a3a3a;
  }
  * { margin: 0; padding: 0; box-sizing: border-box; }
  html, body {
    width: 1200px; height: 900px; overflow: hidden;
    background: var(--stage);
    font-family: "Arimo", Arial, sans-serif;
  }
  .card {
    position: absolute;
    left: 250px;
    width: 700px; height: 400px;
    border-radius: 22px;
    overflow: hidden;
  }
  .card--back { top: 40px; background: var(--card-back); }
  .card--front { top: 460px; background: var(--card); }

  .brand-name {
    position: absolute;
    font-weight: 700;
    text-transform: uppercase;
    line-height: 1;
    display: flex; align-items: center; gap: 14px;
  }
  .brand-name__mark { width: 18px; height: 18px; flex: none; }
  .brand-name__text { display: flex; flex-direction: column; gap: 8px; }

  .card--back .brand-name {
    left: 0; right: 0; top: 150px; justify-content: center;
    color: var(--emboss); font-size: 44px;
  }
  .card--back .brand-name__mark { background: var(--emboss); width: 22px; height: 22px; }
  .card--back .brand-name__text span:last-child { font-size: 26px; letter-spacing: 3px; }

  .card--front .brand-name {
    left: 60px; top: 140px;
    color: var(--ink-light); font-size: 30px;
  }
  .card--front .brand-name__mark { background: var(--ink-light); }
  .card--front .brand-name__text span:last-child { font-size: 18px; letter-spacing: 2px; }

  .divider {
    position: absolute; left: 365px; top: 72px;
    width: 1px; height: 150px; background: var(--brand-blue);
  }
  .contact {
    position: absolute; left: 390px; top: 58px;
    color: var(--ink-soft); font-size: 13px; line-height: 1.3;
  }
  .contact__name {
    color: var(--brand-blue); font-weight: 700; font-size: 21px;
    text-transform: uppercase; line-height: 1.1;
  }
  .contact__role { font-size: 14px; margin-bottom: 12px; }
  .contact__address { margin-bottom: 10px; }
  .contact__line { display: flex; align-items: center; gap: 7px; margin-bottom: 2px; }
  .contact__icon { width: 12px; height: 12px; fill: var(--brand-blue); flex: none; }

  .wave { position: absolute; inset: 0; width: 700px; height: 400px; }
  .wave__band { fill: var(--brand-blue); }
  .wave__line { fill: none; stroke: var(--ink-light); stroke-width: 5; }
</style>
</head>
<body>

  <section class="card card--back" aria-label="Card back">
    <div class="brand-name">
      <span class="brand-name__mark"></span>
      <span class="brand-name__text"><span>Harlow Ridge</span><span>Builders</span></span>
    </div>
  </section>

  <section class="card card--front" aria-label="Card front">
    <svg class="wave" viewBox="0 0 700 400" aria-hidden="true">
      <path class="wave__line" d="M330,345 C450,312 560,262 615,240 C650,226 680,222 700,224"/>
      <path class="wave__band" d="M0,400 L0,362 C180,352 330,342 450,306 C560,272 630,240 700,236 L700,400 Z"/>
    </svg>

    <div class="brand-name">
      <span class="brand-name__mark"></span>
      <span class="brand-name__text"><span>Harlow Ridge</span><span>Builders</span></span>
    </div>

    <div class="divider"></div>

    <div class="contact">
      <p class="contact__name">Daniel Marsh</p>
      <p class="contact__role">CEO/Founder</p>
      <p class="contact__address">48 Fernleigh St,<br>Oakvale, VIC 3190</p>
      <p class="contact__line">
        <svg class="contact__icon" viewBox="0 0 24 24"><path d="M6.6 10.8a15 15 0 0 0 6.6 6.6l2.2-2.2a1 1 0 0 1 1-.25 11.4 11.4 0 0 0 3.6.6 1 1 0 0 1 1 1V20a1 1 0 0 1-1 1A17 17 0 0 1 3 4a1 1 0 0 1 1-1h3.5a1 1 0 0 1 1 1c0 1.25.2 2.45.6 3.6a1 1 0 0 1-.25 1z"/></svg>
        0400 555 018
      </p>
      <p class="contact__line">
        <svg class="contact__icon" viewBox="0 0 24 24"><path d="M2 5h20v14H2z M2 5l10 8 10-8" fill="none" stroke="#3a8bd0" stroke-width="2.5"/></svg>
        info@harlowridgebuild.com.au
      </p>
      <p class="contact__line">
        <svg class="contact__icon" viewBox="0 0 24 24"><circle cx="12" cy="12" r="9" fill="none" stroke="#3a8bd0" stroke-width="2.5"/><path d="M3 12h18M12 3c3 3 3 15 0 18M12 3c-3 3-3 15 0 18" fill="none" stroke="#3a8bd0" stroke-width="2"/></svg>
        harlowridgebuild.com.au
      </p>
    </div>
  </section>

</body>
</html>
```